Vantiqo custom business card design

Need a authentic, innovative business card design for a new mobile app business. I am uploading a few screen images from our app for you to view. I would like app design theme to match business card design. I can also send logo images.

```html
<!DOCTYPE html>
<html lang="en">
<head>
<meta charset="utf-8">
<title>Vantiqo business card</title>
<link rel="stylesheet" href="https://fonts.googleapis.com/css2?family=Montserrat:wght@600;800&family=Source+Sans+3:wght@400&display=swap">
<style>
  :root {
    --backdrop: #141414;
    --card: #1e1e1e;
    --card-edge: #2a2a2a;
    --ink: #e9e9e9;
    --ink-soft: #cfcfcf;
    --accent: #6a1fa3;
    --accent-bright: #7d2bbd;
    --silver: #c9c9c9;
  }
  * { box-sizing: border-box; margin: 0; padding: 0; }
  html, body { width: 1200px; height: 900px; overflow: hidden; }
  body {
    background: var(--backdrop);
    font-family: "Source Sans 3", "Helvetica Neue", Arial, sans-serif;
    color: var(--ink-soft);
    position: relative;
  }
  .card {
    position: absolute;
    left: 290px;
    width: 620px;
    height: 354px;
    background: var(--card);
    border: 1px solid var(--card-edge);
    border-radius: 22px;
    box-shadow: 0 14px 34px rgba(0,0,0,.55);
  }
  .card--back { top: 70px; }
  .card--front { top: 476px; }

  /* back */
  .back-mark {
    position: absolute; left: 0; right: 0; top: 108px;
    display: flex; align-items: center; justify-content: center; gap: 14px;
  }
  .mark-dot {
    width: 30px; height: 30px; border-radius: 50%;
    background: var(--silver);
  }
  .back-mark .brand-name { color: var(--silver); }
  .brand-name {
    font-family: "Montserrat", Arial, sans-serif;
    font-weight: 800;
    font-size: 46px;
    letter-spacing: .5px;
    color: var(--ink);
  }
  .back-url {
    position: absolute; left: 0; right: 0; top: 268px;
    text-align: center; font-size: 15px; color: var(--ink);
  }

  /* front */
  .front-brand {
    position: absolute; right: 44px; top: 50px;
    display: flex; align-items: center; gap: 12px;
  }
  .front-brand .mark-dot { background: var(--accent); width: 34px; height: 34px; }
  .address {
    position: absolute; right: 44px; top: 138px;
    text-align: right; font-size: 17px; line-height: 1.25; color: var(--ink);
  }
  .holder { position: absolute; left: 44px; top: 196px; }
  .holder-name {
    font-family: "Montserrat", Arial, sans-serif;
    font-weight: 600; font-size: 21px; color: var(--accent-bright);
    text-transform: uppercase; letter-spacing: .3px;
  }
  .holder-role { font-size: 17px; color: var(--ink-soft); margin-top: 1px; }
  .contacts { list-style: none; margin-top: 14px; }
  .contacts li {
    display: flex; align-items: center; gap: 8px;
    font-size: 18px; line-height: 1.3; color: var(--ink);
  }
  .contacts svg { width: 15px; height: 15px; fill: var(--accent-bright); flex: none; }
</style>
</head>
<body>
  <section class="card card--back" aria-label="Card back">
    <div class="back-mark">
      <span class="mark-dot"></span>
      <span class="brand-name">Vantiqo</span>
    </div>
    <p class="back-url">www.vantiqoapp.com</p>
  </section>

  <section class="card card--front" aria-label="Card front">
    <div class="front-brand">
      <span class="mark-dot"></span>
      <span class="brand-name">Vantiqo</span>
    </div>
    <p class="address">48 Lantern Row, Suite 12<br>Westbrook, 40512</p>

    <div class="holder">
      <h1 class="holder-name">Marcus Ellery</h1>
      <p class="holder-role">Managing Director</p>
      <ul class="contacts">
        <li>
          <svg viewBox="0 0 16 16" aria-hidden="true"><path d="M1 5c0-2 3-3 7-3s7 1 7 3v1h-3.5V4.5h-7V6H1zM3 7h10l1.5 7h-13zM8 8.5a2 2 0 1 0 0 4 2 2 0 0 0 0-4z"/></svg>
          044-718 302 655
        </li>
        <li>
          <svg viewBox="0 0 16 16" aria-hidden="true"><path d="M4.5 1h7a1 1 0 0 1 1 1v12a1 1 0 0 1-1 1h-7a1 1 0 0 1-1-1V2a1 1 0 0 1 1-1zm1 2v9h5V3zM8 12.6a.8.8 0 1 0 0 1.6.8.8 0 0 0 0-1.6z"/></svg>
          044-718 302 655
        </li>
        <li>
          <svg viewBox="0 0 16 16" aria-hidden="true"><path d="M1 3h14v1.2L8 9 1 4.2zM1 5.8l7 4.8 7-4.8V13H1z"/></svg>
          hello@vantiqoapp.com
        </li>
      </ul>
    </div>
  </section>
</body>
</html>
```